tinyTally Resource Book - 10 maths tasks to do outside

I need a 22 (11 pages back to back) page A6 sized book produced to standard for submission to professional printer. Needs to be as .pdf file showing guide lines and allowances for colour bleed. I have text already written and submitted as attachment in a Word file with margins set to A6 size. The theme of the materials is "Nature Play" so using lots of pictures from nature (Australia preferably) and showing lots of patterns in nature (rocks, leaves, flower petals etc). Some of the tasks refer to specific activities, such as "shadows" and "floating" so would be great to illustrate appropriately. The big emphasis is on learning outside the classroom, getting kids to engage actively with nature. I would like to see the pages as full colour - so not white background. The book itself will be spiral bound along the top edge so a margin of at least 1cm will be required at the top of each page (or the bottom of even numbered pages). Book will be printed on plastic laminated matte paper for outdoor use. Font size needs to be big enough to read. Fonts sizes, alignments and page numbers are all different at the moment and need to be standardised. One photo is included in a page as a sample if you can use it, otherwise disregard. Logo for Wattlebrook Numeracy Guild is also included to have as part of the acknowledgements at the back of the book.

Target Market(s)

Book is for early childhood and preschool teachers.

Industry/Entity Type

Education

Font styles to use
Sans Serif

Requirements
Must have
• Colour and appeal.
Nice to have
• Use of natural colours instead of bright catchy colours but that is your call.
Should not have
• American spelling

```html
<!DOCTYPE html>
<html lang="en-AU">
<head>
<meta charset="utf-8">
<title>Big Bigger Biggest – Task 2</title>
<link rel="stylesheet" href="https://fonts.googleapis.com/css2?family=Nunito:wght@900&family=Jost:wght@400&display=swap">
<style>
  :root {
    --paper: #ffffff;
    --trim-line: #333333;
    --wood-light: #d9bf9c;
    --wood-mid: #c39a72;
    --wood-dark: #8f5b3c;
    --bark-grey: #6d6a66;
    --wash: rgba(255, 250, 244, 0.45);
    --heading-blue: #2b3a97;
    --body-ink: #3a3530;
    --bullet-red: #d8232a;
    --outline-white: #ffffff;
  }
  html, body {
    margin: 0;
    padding: 0;
    width: 825px;
    height: 1200px;
    overflow: hidden;
    background: var(--paper);
  }
  .canvas {
    position: relative;
    width: 825px;
    height: 1200px;
  }
  .trim-marks {
    position: absolute;
    inset: 0;
  }
  .page {
    position: absolute;
    left: 50px;
    top: 56px;
    width: 726px;
    height: 1092px;
    overflow: hidden;
  }
  .page__photo {
    position: absolute;
    inset: 0;
    background:
      radial-gradient(ellipse 45% 25% at 65% 28%, var(--wood-light), transparent 75%),
      radial-gradient(ellipse 40% 22% at 25% 45%, var(--wood-mid), transparent 75%),
      radial-gradient(ellipse 55% 30% at 70% 85%, var(--wood-dark), transparent 75%),
      radial-gradient(ellipse 35% 20% at 15% 90%, var(--wood-mid), transparent 75%),
      linear-gradient(160deg, var(--wood-mid), var(--bark-grey));
  }
  .page__wash {
    position: absolute;
    inset: 0;
    background: var(--wash);
  }
  .heading {
    position: absolute;
    left: 66px;
    margin: 0;
    font-family: "Nunito", sans-serif;
    font-weight: 900;
    color: var(--heading-blue);
    -webkit-text-stroke: 6px var(--outline-white);
    paint-order: stroke fill;
    line-height: 1;
    letter-spacing: 0.2px;
  }
  .heading--title { top: 88px; font-size: 50px; }
  .heading--section { font-size: 45px; }
  .heading--prompts { top: 410px; }
  .heading--variations { top: 644px; }
  .heading--ideas { top: 798px; }
  .task-list {
    position: absolute;
    left: 152px;
    width: 540px;
    margin: 0;
    padding: 0;
    list-style: none;
    font-family: "Jost", sans-serif;
    font-weight: 400;
    font-size: 29px;
    line-height: 42px;
    color: var(--body-ink);
  }
  .task-list li {
    position: relative;
  }
  .task-list li::before {
    content: "";
    position: absolute;
    left: -29px;
    top: 13px;
    width: 15px;
    height: 15px;
    background: var(--bullet-red);
    transform: rotate(45deg);
  }
  .task-list--steps { top: 145px; }
  .task-list--prompts { top: 466px; }
  .task-list--variations { top: 701px; }
  .task-list--ideas { top: 855px; }
  .page-number {
    position: absolute;
    left: 595px;
    top: 970px;
    width: 64px;
    height: 64px;
  }
</style>
</head>
<body>
<div class="canvas">
  <svg class="trim-marks" width="825" height="1200" viewBox="0 0 825 1200" aria-hidden="true">
    <g stroke="var(--trim-line)" stroke-width="0.8" fill="none">
      <line x1="50" y1="0" x2="50" y2="40"/><line x1="68" y1="0" x2="68" y2="40"/>
      <line x1="0" y1="56" x2="34" y2="56"/><line x1="0" y1="74" x2="34" y2="74"/>
      <line x1="776" y1="0" x2="776" y2="40"/><line x1="758" y1="0" x2="758" y2="40"/>
      <line x1="792" y1="56" x2="825" y2="56"/><line x1="792" y1="74" x2="825" y2="74"/>
      <line x1="50" y1="1164" x2="50" y2="1200"/><line x1="68" y1="1164" x2="68" y2="1200"/>
      <line x1="0" y1="1148" x2="34" y2="1148"/><line x1="0" y1="1130" x2="34" y2="1130"/>
      <line x1="776" y1="1164" x2="776" y2="1200"/><line x1="758" y1="1164" x2="758" y2="1200"/>
      <line x1="792" y1="1148" x2="825" y2="1148"/><line x1="792" y1="1130" x2="825" y2="1130"/>
    </g>
  </svg>

  <section class="page">
    <div class="page__photo" role="img" aria-label="Photograph of stacked cut log ends showing tree rings in warm browns"></div>
    <div class="page__wash"></div>

    <h1 class="heading heading--title">2. Big Bigger Biggest</h1>
    <ul class="task-list task-list--steps">
      <li>Find an object – stone, leaf, stick etc</li>
      <li>Now find a bigger one</li>
      <li>Now find an even bigger one than that</li>
      <li>Line them up – big bigger biggest</li>
      <li>Keep adding to your line</li>
    </ul>

    <h2 class="heading heading--section heading--prompts">Prompting questions</h2>
    <ul class="task-list task-list--prompts">
      <li>Where do you put new rocks in the line?</li>
      <li>Can you take away some rocks to make your “biggest” the “smallest”?</li>
    </ul>

    <h2 class="heading heading--section heading--variations">Variations</h2>
    <ul class="task-list task-list--variations">
      <li>Small Smaller Smallest</li>
      <li>Long Longer Longest</li>
    </ul>

    <h2 class="heading heading--section heading--ideas">Big Ideas</h2>
    <ul class="task-list task-list--ideas">
      <li>Comparison</li>
      <li>Visualisation</li>
      <li>Prediction</li>
    </ul>

    <svg class="page-number" viewBox="0 0 64 64" aria-label="Page 5">
      <polygon points="32,2 62,24 51,61 13,61 2,24" fill="var(--heading-blue)"/>
      <text x="32" y="46" text-anchor="middle" font-family="Jost, sans-serif" font-size="28" fill="#ffffff">5</text>
    </svg>
  </section>
</div>
</body>
</html>
```